Landing page design for my current website

I need a landing page designed for my Wordpress website. My website is Velmorquay.com, and I need a page that will serve as a landing page for online ads I run. Please follow the color scheme of the current website

This web page will be targeted towards real estate owners who are looking for a property manager. Above the fold needs to have a CTA form headlined with "As a Rental Property Owner, I Want More Protection, Less Stress, and Drama-Free Living"

A few highlights that can be listed beyond the CTA and fold

- Comprehensive Property Management
Full-service management covering tenant placement, leasing, maintenance, and inspections.

Maximized Rental Income
Proven strategies to optimize rental rates and minimize vacancies, ensuring higher ROI.

Stress-Free Management
We handle all tenant interactions, maintenance requests, and property issues, so you don't have to.

Experienced Team
Over a decade of experience in managing single-family homes, small multifamily units, and apartment complexes.

Advanced Technology
Utilize cutting-edge property management software for efficient communication, rent collection, and maintenance tracking.

Tenant Screening and Placement
Thorough background checks and tenant screening processes to ensure reliable and responsible tenants.

Regular Property Inspections
Routine inspections to maintain property condition and address issues before they become costly problems.

Legal Compliance
Expertise in local and federal rental laws to keep your properties compliant and avoid legal hassles.

Transparent Reporting
Detailed monthly reports and financial statements to keep you informed about your property's performance.

Personalized Service
Tailored management plans to meet the unique needs of your properties and investment goals.
Effective Tenant Conflict Resolution
Skilled in handling challenging tenant situations, ensuring conflicts are resolved quickly and professionally to maintain a peaceful living environment and protect your investment.

```html
<!DOCTYPE html>
<html lang="en">
<head>
<meta charset="utf-8">
<title>Velmorquay Realty – Property Management</title>
<link href="https://fonts.googleapis.com/css2?family=Poppins:wght@400;500;600;700;800&display=swap" rel="stylesheet">
<style>
:root{
  --navy:#1a4379;
  --orange:#ff6b00;
  --ink:#2b2b2b;
  --text:#3a3a3a;
  --card:#f3f3f3;
  --footer:#2b2b2b;
  --white:#ffffff;
}
*{box-sizing:border-box;margin:0;padding:0}
html,body{width:1200px;height:2334px;overflow:hidden}
body{font-family:"Poppins",sans-serif;background:var(--white);color:var(--text);position:relative}

.site-header{position:absolute;top:0;left:0;width:1200px;height:82px;background:var(--white)}
.brand{position:absolute;left:75px;top:22px;display:flex;align-items:center;gap:9px}
.brand-dot{width:38px;height:38px;border-radius:50%;border:2px solid var(--navy)}
.brand-name{font-size:19px;font-weight:600;color:var(--navy);letter-spacing:.5px}
.main-nav{position:absolute;left:409px;top:33px;display:flex;gap:31px;font-size:15px;font-weight:500;color:var(--ink)}
.main-nav .active{color:var(--navy)}
.call{position:absolute;left:936px;top:23px;display:flex;align-items:center;gap:11px}
.call-icon{width:36px;height:36px;border-radius:50%;background:var(--navy);display:flex;align-items:center;justify-content:center}
.call-label{font-size:14px;font-weight:500;color:var(--ink);line-height:16px}
.call-number{font-size:21px;font-weight:600;color:var(--navy);line-height:24px}

.hero{position:absolute;top:82px;left:0;width:1200px;height:638px;overflow:hidden}
.hero-photo{position:absolute;inset:0;background:linear-gradient(180deg,#5c6d8f 0%,#8a8fa2 35%,#8a7760 65%,#3f4a2d 100%)}
.hero-shade{position:absolute;inset:0;background:linear-gradient(90deg,rgba(20,28,45,.45),rgba(20,28,45,.15))}
.hero-copy{position:absolute;left:73px;top:169px;width:610px;color:var(--white)}
.hero-copy h1{font-size:51px;font-weight:800;line-height:52px;letter-spacing:.5px}
.hero-copy p{font-size:20px;line-height:28px;margin-top:14px}
.btn-outline{display:inline-block;margin-top:24px;margin-left:2px;border:2px solid var(--white);padding:11px 24px;font-size:17px;font-weight:700;color:var(--white)}
.dots{position:absolute;left:75px;top:572px;display:flex;gap:9px}
.dots span{width:10px;height:10px;border-radius:2px;background:var(--white)}
.dots .on{background:var(--orange)}

.lead-form{position:absolute;left:793px;top:64px;width:333px;height:512px;background:var(--white);border-radius:12px;padding:18px 19px}
.lead-form h2{font-size:20px;font-weight:700;line-height:27px;color:var(--navy);text-align:center}
.field{display:block;width:294px;height:51px;border:1px solid #8a8a8a;margin-top:11px;padding:18px 14px 0;font-size:12px;color:#333}
.field:first-of-type{margin-top:19px}
.field.msg{height:102px;padding-top:13px}
.submit{display:flex;align-items:center;justify-content:center;width:294px;height:51px;margin-top:10px;background:var(--orange);color:var(--white);font-size:20px;font-weight:700}

.features{position:absolute;left:75px;top:794px;width:1051px;display:grid;grid-template-columns:512px 512px;column-gap:27px;row-gap:22px;align-items:start}
.feature{position:relative;padding-left:49px}
.feature-card{min-height:239px;background:var(--card);border-radius:60px;padding:30px 30px 30px 65px;display:flex;flex-direction:column;justify-content:center}
.feature-card h3{font-size:26px;font-weight:600;line-height:30px;color:var(--navy)}
.feature-card p{font-size:15px;line-height:25px;margin-top:10px;color:var(--text)}
.feature-icon{position:absolute;left:0;top:50%;margin-top:-46px;width:92px;height:92px;border-radius:50%;background:var(--navy);display:flex;align-items:center;justify-content:center}
.feature.tall .feature-card{min-height:275px}

.site-footer{position:absolute;left:0;top:2178px;width:1200px;height:156px;background:var(--footer);text-align:center;color:var(--white)}
.site-footer p{font-size:14px;margin-top:52px}
.social{display:flex;justify-content:center;gap:20px;margin-top:20px}
.social span{width:20px;height:20px;border-radius:50%;background:var(--white)}
</style>
</head>
<body>

<header class="site-header">
  <div class="brand"><span class="brand-dot"></span><span class="brand-name">VELMORQUAY REALTY</span></div>
  <nav class="main-nav">
    <span class="active">Home</span><span>Residents</span><span>Investors</span><span>Communities</span><span>Contact Us</span>
  </nav>
  <div class="call">
    <span class="call-icon"><svg width="18" height="18" viewBox="0 0 24 24" fill="none" stroke="#fff" stroke-width="2"><path d="M5 3h4l2 5-3 2a11 11 0 0 0 6 6l2-3 5 2v4a2 2 0 0 1-2 2A18 18 0 0 1 3 5a2 2 0 0 1 2-2z"/></svg></span>
    <div><div class="call-label">Call or Text</div><div class="call-number">555.014.2870</div></div>
  </div>
</header>

<section class="hero">
  <div class="hero-photo" role="img" aria-label="Two-storey suburban house with lit windows and a green lawn at dusk"></div>
  <div class="hero-shade"></div>
  <div class="hero-copy">
    <h1>HOMES &amp; APARTMENTS FOR RENT</h1>
    <p>Velmorquay, Inc. offers affordable, safe, up-to-date housing options in the Bloomsburg, Danville, and Berwick Pennsylvania markets. Contact us today if you’re looking for your next rental.</p>
    <span class="btn-outline">READ MORE</span>
  </div>
  <div class="dots"><span></span><span class="on"></span><span></span><span></span></div>
  <form class="lead-form">
    <h2>As a Rental Property Owner, I Want More Protection, Less Stress, and Drama-Free Living</h2>
    <span class="field">Name</span>
    <span class="field">Email Address</span>
    <span class="field">Phone No</span>
    <span class="field msg">Message</span>
    <span class="submit">Submit</span>
  </form>
</section>

<main class="features">
  <div class="feature"><span class="feature-icon"><svg width="48" height="48" viewBox="0 0 48 48" fill="none" stroke="#fff" stroke-width="2"><path d="M6 26l12-10 12 10M10 23v17h16V23"/><rect x="26" y="6" width="16" height="22"/><path d="M30 12h8M30 17h8M30 22h5"/></svg></span>
    <div class="feature-card"><h3>Comprehensive Property Management</h3><p>Full-service management covering tenant placement, leasing, maintenance, and inspections.</p></div></div>
  <div class="feature"><span class="feature-icon"><svg width="48" height="48" viewBox="0 0 48 48" fill="none" stroke="#fff" stroke-width="2"><path d="M6 20L24 6l18 14M10 17v23h28V17"/><rect x="14" y="28" width="20" height="9"/><path d="M18 18h12v6H18z"/></svg></span>
    <div class="feature-card"><h3>Maximized Rental Income</h3><p>Proven strategies to optimize rental rates and minimize vacancies, ensuring higher ROI.</p></div></div>
  <div class="feature"><span class="feature-icon"><svg width="48" height="48" viewBox="0 0 48 48" fill="none" stroke="#fff" stroke-width="2"><circle cx="24" cy="12" r="5"/><path d="M15 26a9 9 0 0 1 18 0"/><rect x="6" y="28" width="12" height="14"/><circle cx="36" cy="35" r="6"/><path d="M20 35h8"/></svg></span>
    <div class="feature-card"><h3>Stress-Free Management</h3><p>We handle all tenant interactions, maintenance requests, and property issues, so you don't have to.</p></div></div>
  <div class="feature"><span class="feature-icon"><svg width="48" height="48" viewBox="0 0 48 48" fill="none" stroke="#fff" stroke-width="2"><circle cx="24" cy="16" r="9"/><circle cx="16" cy="30" r="4"/><circle cx="32" cy="30" r="4"/><path d="M8 42v-4a8 8 0 0 1 16 0v4M24 42v-4a8 8 0 0 1 16 0v4"/></svg></span>
    <div class="feature-card"><h3>Experienced Team</h3><p>Over a decade of experience in managing single-family homes, small multifamily units, and apartment complexes.</p></div></div>
  <div class="feature"><span class="feature-icon"><svg width="48" height="48" viewBox="0 0 48 48" fill="none" stroke="#fff" stroke-width="2"><circle cx="28" cy="18" r="8"/><circle cx="28" cy="18" r="3"/><path d="M18 26a10 10 0 0 0 3 8v6h8M6 12l4 2M4 22h5M6 32l4-2"/></svg></span>
    <div class="feature-card"><h3>Advanced Technology</h3><p>Utilize cutting-edge property management software for efficient communication, rent collection, and maintenance tracking.</p></div></div>
  <div class="feature"><span class="feature-icon"><svg width="48" height="48" viewBox="0 0 48 48" fill="none" stroke="#fff" stroke-width="2"><path d="M4 22L16 12l12 10M8 19v12h16V19"/><circle cx="34" cy="16" r="6"/><path d="M24 40a10 10 0 0 1 20 0"/><circle cx="10" cy="38" r="4"/><path d="M14 38h8"/></svg></span>
    <div class="feature-card"><h3>Tenant Screening and Placement</h3><p>Thorough background checks and tenant screening processes to ensure reliable and responsible tenants.</p></div></div>
  <div class="feature"><span class="feature-icon"><svg width="48" height="48" viewBox="0 0 48 48" fill="none" stroke="#fff" stroke-width="2"><rect x="8" y="14" width="14" height="28"/><rect x="22" y="6" width="18" height="36"/><path d="M12 20h6M12 27h6M27 12h8M27 19h8M27 26h8M28 42v-8h6v8"/></svg></span>
    <div class="feature-card"><h3>Regular Property Inspections</h3><p>Routine inspections to maintain property condition and address issues before they become costly problems.</p></div></div>
  <div class="feature"><span class="feature-icon"><svg width="48" height="48" viewBox="0 0 48 48" fill="none" stroke="#fff" stroke-width="2"><rect x="8" y="6" width="22" height="30"/><path d="M13 14h12M13 20h12M13 26h6"/><path d="M28 32l8-8 4 4-8 8zM34 34l8 8"/><path d="M6 42h20"/></svg></span>
    <div class="feature-card"><h3>Legal Compliance</h3><p>Expertise in local and federal rental laws to keep your properties compliant and avoid legal hassles.</p></div></div>
  <div class="feature"><span class="feature-icon"><svg width="48" height="48" viewBox="0 0 48 48" fill="none" stroke="#fff" stroke-width="2"><rect x="10" y="6" width="28" height="36"/><circle cx="18" cy="15" r="4"/><path d="M26 13h8M26 18h8M15 36v-6M20 36v-9M25 36v-4M30 26h4M30 31h4"/></svg></span>
    <div class="feature-card"><h3>Transparent Reporting</h3><p>Detailed monthly reports and financial statements to keep you informed about your property's performance.</p></div></div>
  <div class="feature tall"><span class="feature-icon"><svg width="48" height="48" viewBox="0 0 48 48" fill="none" stroke="#fff" stroke-width="2"><circle cx="20" cy="20" r="13"/><circle cx="20" cy="17" r="4"/><path d="M12 28a8 8 0 0 1 16 0"/><rect x="26" y="28" width="16" height="14"/><path d="M29 33h10M29 38h10"/></svg></span>
    <div class="feature-card"><h3>Personalized Service</h3><p>Tailored management plans to meet the unique needs of your properties and investment goals. Effective Tenant Conflict ResolutionSkilled in handling challenging tenant situations, ensuring conflicts are resolved quickly and professionally to maintain a peaceful living environment and protect your investment.</p></div></div>
</main>

<footer class="site-footer">
  <p>Company © 2024 Company Name All Right Reserved</p>
  <div class="social">
    <span aria-label="Social profile"></span><span aria-label="Social profile"></span><span aria-label="Social profile"></span><span aria-label="Social profile"></span><span aria-label="Social profile"></span>
  </div>
</footer>

</body>
</html>
```